Keystone Trench Co Business Card*

Looking for a professional, clean and crisp business card

I am in the underground utilities industry and am just looking for a really impressive business card. I would like our card to be white with our symbol crisp and clear with it protruding. I also have a business partner that will require his name and info on the card once the design is set. I would like to have our website info on the card which is;
http://keystonetrenchco.example/

Contact Information for Business Card

Website, contact name, number and email

```html
<!DOCTYPE html>
<html lang="en">
<head>
<meta charset="utf-8">
<title>Keystone Trench Co — Business Card</title>
<link href="https://fonts.googleapis.com/css2?family=Roboto+Condensed:wght@400;700&display=swap" rel="stylesheet">
<style>
  :root {
    --backdrop: #000000;
    --card: #ffffff;
    --card-stripe: #f7f7f7;
    --ink: #2d2e30;
    --ink-soft: #3c3d40;
    --rule: #b5b6b8;
  }
  * { box-sizing: border-box; margin: 0; padding: 0; }
  html, body { width: 1200px; height: 900px; overflow: hidden; background: var(--backdrop); }
  .canvas {
    position: relative;
    width: 1200px;
    height: 900px;
    background: var(--backdrop);
    font-family: "Roboto Condensed", "Arial Narrow", sans-serif;
    color: var(--ink);
  }
  .card {
    position: absolute;
    top: 266px;
    width: 458px;
    height: 282px;
    border-radius: 14px;
    background:
      repeating-linear-gradient(90deg, var(--card) 0 2px, var(--card-stripe) 2px 3px);
  }
  .card--front { left: 138px; }
  .card--back { left: 625px; }

  .brand {
    position: absolute;
    display: flex;
    flex-direction: column;
    align-items: center;
    gap: 8px;
    text-align: center;
  }
  .card--front .brand { left: 42px; top: 82px; width: 140px; }
  .card--back .brand { left: 159px; top: 82px; width: 140px; }
  .brand__dot {
    width: 40px;
    height: 40px;
    border-radius: 50%;
    background: var(--ink);
  }
  .brand__name {
    font-weight: 700;
    font-size: 21px;
    line-height: 1.05;
    letter-spacing: 0.5px;
    text-transform: uppercase;
    color: var(--ink);
  }

  .divider {
    position: absolute;
    left: 214px;
    top: 88px;
    width: 1px;
    height: 105px;
    background: var(--rule);
  }

  .contact {
    position: absolute;
    left: 233px;
    top: 85px;
    color: var(--ink);
  }
  .contact__name {
    font-weight: 700;
    font-size: 19px;
    line-height: 1;
    letter-spacing: 0.2px;
    text-transform: uppercase;
    color: var(--ink);
  }
  .contact__role {
    font-size: 15px;
    line-height: 1.1;
    color: var(--ink-soft);
    margin-top: 2px;
  }
  .contact__list {
    list-style: none;
    margin-top: 21px;
  }
  .contact__item {
    display: flex;
    align-items: center;
    gap: 5px;
    font-size: 14.5px;
    line-height: 17.5px;
    color: var(--ink-soft);
    white-space: nowrap;
  }
  .contact__icon { width: 13px; height: 13px; flex: none; color: var(--ink); }
</style>
</head>
<body>
<main class="canvas">

  <section class="card card--front" aria-label="Business card front">
    <div class="brand">
      <span class="brand__dot" aria-hidden="true"></span>
      <span class="brand__name">Keystone<br>Trench Co</span>
    </div>

    <span class="divider" aria-hidden="true"></span>

    <div class="contact">
      <h1 class="contact__name">Daniel Whitfield</h1>
      <p class="contact__role">Managing Director</p>
      <ul class="contact__list">
        <li class="contact__item">
          <svg class="contact__icon" viewBox="0 0 24 24" aria-hidden="true"><path fill="none" stroke="currentColor" stroke-width="2.2" d="M6 2l4 5-2.5 2.5a12 12 0 0 0 7 7L17 14l5 4-2.5 3.5C11 22 2 13 2.5 4.5z"/></svg>
          044-555 012 347
        </li>
        <li class="contact__item">
          <svg class="contact__icon" viewBox="0 0 24 24" aria-hidden="true"><rect x="1" y="4" width="22" height="16" fill="currentColor"/><path d="M1 4l11 9 11-9" fill="none" stroke="#ffffff" stroke-width="2"/></svg>
          info@keystonetrenchco.example
        </li>
        <li class="contact__item">
          <svg class="contact__icon" viewBox="0 0 24 24" aria-hidden="true"><g fill="none" stroke="currentColor" stroke-width="1.8"><circle cx="12" cy="12" r="10.5"/><ellipse cx="12" cy="12" rx="4.5" ry="10.5"/><path d="M1.5 12h21M3.5 6.5h17M3.5 17.5h17"/></g></svg>
          www.keystonetrenchco.example
        </li>
      </ul>
    </div>
  </section>

  <section class="card card--back" aria-label="Business card back">
    <div class="brand">
      <span class="brand__dot" aria-hidden="true"></span>
      <span class="brand__name">Keystone<br>Trench Co</span>
    </div>
  </section>

</main>
</body>
</html>
```